Maple Roster Business Card for recruitment company

We are looking for a Business Card Design that incorporates our personal details and our busines name and logo. We are a specialized search consultancy that recruit Property and Construction professionals.
We would like a business card that stands out and is appealing to the Construction and Property industry as well.

Target Market(s)

people in the construction and property industry

Contact Information for Business Card

Business Name and logo

Font styles to use
Serif

Colors
0094D4
00A9DD
6FCCEA
C7EBF8
E9F6FB

Requirements
Must have
• Business name and logo as well as contact details
Should not have
• No photos of us please

```html
<!DOCTYPE html>
<html lang="en">
<head>
<meta charset="utf-8">
<title>Maple Roster Business Card</title>
<link rel="stylesheet" href="https://fonts.googleapis.com/css2?family=Josefin+Sans:wght@400&family=Montserrat:wght@500;600;700&display=swap">
<style>
  :root {
    --ink: #053d52;
    --text: #1e1e1e;
    --stage: #d8d8d8;
    --card: #ffffff;
    --watermark: #e4e4e4;
  }
  * { margin: 0; padding: 0; box-sizing: border-box; }
  html, body { width: 800px; height: 1200px; overflow: hidden; }
  body {
    background: var(--stage);
    font-family: "Montserrat", sans-serif;
    color: var(--text);
    position: relative;
  }
  .card {
    position: absolute;
    left: 80px;
    width: 640px;
    height: 365px;
    background: var(--card);
    overflow: hidden;
    box-shadow: 0 6px 18px rgba(0,0,0,0.28);
  }
  .card--front { top: 195px; }
  .card--back { top: 640px; }

  .faint-disc {
    position: absolute;
    border-radius: 50%;
    background: var(--watermark);
  }
  .card--front .faint-disc { left: 0; top: 233px; width: 172px; height: 172px; transform: translateX(-50%); }
  .card--back .faint-disc { left: 368px; top: 77px; width: 268px; height: 268px; }

  .accent-bar {
    position: absolute;
    left: 88px;
    width: 466px;
    bottom: 0;
    height: 6px;
    background: var(--ink);
    border-radius: 4px 4px 0 0;
  }

  .brand-name {
    font-family: "Josefin Sans", sans-serif;
    font-weight: 400;
    color: var(--ink);
    text-transform: uppercase;
    white-space: nowrap;
    line-height: 1;
  }
  .card--front .brand-name {
    position: absolute;
    top: 126px;
    left: 0;
    width: 100%;
    text-align: center;
    font-size: 64px;
    letter-spacing: 1px;
  }
  .card--front .web-address {
    position: absolute;
    top: 303px;
    left: 0;
    width: 100%;
    text-align: center;
    font-size: 20px;
    font-weight: 600;
    letter-spacing: 1.5px;
  }

  .card--back .brand-name {
    position: absolute;
    top: 64px;
    left: 40px;
    font-size: 40px;
    letter-spacing: 0.5px;
  }
  .person-name {
    position: absolute;
    top: 129px;
    left: 40px;
    font-size: 23px;
    font-weight: 700;
    color: var(--ink);
    letter-spacing: 0.8px;
    text-transform: uppercase;
  }
  .person-role {
    position: absolute;
    top: 159px;
    left: 40px;
    font-size: 12.5px;
    font-weight: 500;
    letter-spacing: 0.4px;
  }
  .contact-list {
    position: absolute;
    top: 220px;
    left: 40px;
    list-style: none;
  }
  .contact-list li {
    display: flex;
    align-items: center;
    height: 29px;
    font-size: 17px;
    font-weight: 600;
    letter-spacing: 0.8px;
  }
  .contact-list svg {
    width: 17px;
    height: 17px;
    margin-right: 10px;
    flex: none;
  }
</style>
</head>
<body>

  <section class="card card--front" aria-label="Business card front">
    <div class="faint-disc" aria-hidden="true"></div>
    <div class="brand-name">Maple Roster</div>
    <div class="web-address">www.mapleroster.nz</div>
    <div class="accent-bar"></div>
  </section>

  <section class="card card--back" aria-label="Business card back">
    <div class="faint-disc" aria-hidden="true"></div>
    <div class="brand-name">Maple Roster</div>
    <div class="person-name">Nora Whitfield</div>
    <div class="person-role">Senior Search Consultant</div>
    <ul class="contact-list">
      <li>
        <svg viewBox="0 0 24 24" aria-hidden="true"><path fill="var(--ink)" d="M6.6 10.8c1.4 2.8 3.8 5.1 6.6 6.6l2.2-2.2c.3-.3.7-.4 1-.2 1.1.4 2.3.6 3.6.6.6 0 1 .4 1 1V20c0 .6-.4 1-1 1C10.6 21 3 13.4 3 4c0-.6.4-1 1-1h3.5c.6 0 1 .4 1 1 0 1.3.2 2.5.6 3.6.1.3 0 .7-.2 1z"/><path fill="none" stroke="var(--ink)" stroke-width="1.6" d="M14 7a4 4 0 0 1 3 3M14 3a8 8 0 0 1 7 7"/></svg>
        +64 21 555 0142
      </li>
      <li>
        <svg viewBox="0 0 24 24" aria-hidden="true"><rect x="2" y="5" width="20" height="14" fill="var(--ink)"/><path d="M2.5 5.5 12 13l9.5-7.5M2.5 18.5l7-6M21.5 18.5l-7-6" fill="none" stroke="#fff" stroke-width="1.4"/></svg>
        n.whitfield@mapleroster.nz
      </li>
      <li>
        <svg viewBox="0 0 24 24" aria-hidden="true"><g fill="none" stroke="var(--ink)" stroke-width="1.8"><circle cx="12" cy="12" r="9.5"/><ellipse cx="12" cy="12" rx="4.2" ry="9.5"/><path d="M2.5 12h19M4 7h16M4 17h16"/></g></svg>
        www.mapleroster.nz
      </li>
    </ul>
    <div class="accent-bar"></div>
  </section>

</body>
</html>
```